PSD Only - Wordpress Magazine Theme Design

We need a design for our new Premuim wordpress Magazine theme design based on our basic wire-frame. The theme will be used by people who run online magazine, news website or just blog in general.

The layout of homepage is showing recent posts in many way which is easy to user to customize the section of their homepage to show their post based on various categories.

2 Page design need (Homepage and Single Post)
Updates

Reason: want to get more designer and I am off for holiday a few days too. Better extend the time for designers as well as me also.

Target Market(s)

General Blogger who want a nice premium theme as well as other content based wesite.

Industry/Entity Type

Online

Font styles to use
Sans Serif

Requirements
Must have
• + Must have 2 page design based on Wireframing. Homepage (home.png) annd Single Post (Single.png)
• + Layout must be based on wireframe.
• + Width 1025px
• + 2 Navigation Menu in Header Must be in different style. When theme goes public, user can choose to have both or only 1 navigation or completely hide both of them.
• + 2 Featured Content Slider as you see in wire-frame. They must be in different style from each other.
• + Those recent news section is only about arrange post in defferent ways which only include post feature image, post title as well as post meta info.
• + Sidebar Widget Must be 300px (not include margin or padding) in order to be able for user to place ads with (300px of width) in sidebar widget)
• + Footer Widget Section should have a bit different colour in order to look different for main layout.
Nice to have
• + Drop down Menu
• + (Optional) Some custom Widget (Based on your imagination and creativity)

```html
<!DOCTYPE html>
<html lang="en">
<head>
<meta charset="utf-8">
<title>Nova Magazine – Homepage</title>
<link rel="stylesheet" href="https://fonts.googleapis.com/css2?family=Open+Sans:ital,wght@0,400;0,600;0,700;1,400&display=swap">
<style>
:root{
  --blue:#1f4e8f;
  --blue-dark:#173c70;
  --ink:#222;
  --text:#555;
  --muted:#8a8a8a;
  --rule:#e2e2e2;
  --topbar:#2f2f2f;
  --footer:#2b2b2b;
  --footer-bottom:#1c1c1c;
  --footer-text:#8d8d8d;
}
*{box-sizing:border-box;margin:0;padding:0}
html,body{width:1200px;height:4119px;overflow:hidden;background:#fff}
body{font-family:"Open Sans",Arial,sans-serif;color:var(--text)}
.page{position:relative;width:1200px;height:4119px;overflow:hidden}
.abs{position:absolute}
a{color:inherit;text-decoration:none}

/* top bar */
.topbar{left:0;top:0;width:1200px;height:38px;background:var(--topbar);color:#cfcfcf;font-size:12px}
.topbar .link{position:absolute;top:11px}
.topbar .connect{position:absolute;left:742px;top:11px;color:#a8a8a8}
.topbar .social{position:absolute;top:12px;width:14px;height:14px;border-radius:50%;background:#9a9a9a}

/* header */
.brand{left:162px;top:70px;font-size:33px;font-weight:700;color:var(--ink);letter-spacing:-.5px}
.slogan{left:162px;top:110px;font-size:17px;color:#333}
.ad{left:415px;top:66px;width:623px;height:74px;background:linear-gradient(90deg,#f29a2a 0%,#f5b54a 35%,#3a6fb0 70%,#2a5594 100%)}

/* main nav */
.mainnav{left:162px;top:167px;width:876px;height:42px;background:var(--blue)}
.mainnav .item{position:absolute;top:13px;color:#fff;font-size:12px;font-weight:700}
.search{position:absolute;left:626px;top:8px;width:244px;height:26px;background:var(--blue-dark);color:#c8d3e6;font-size:11px;padding:6px 10px}
.search svg{position:absolute;right:8px;top:6px}

/* hero slider */
.hero{left:162px;top:217px;width:876px;height:308px;background:linear-gradient(100deg,#d9d9d9 0%,#8a8a8a 30%,#2e2e2e 55%,#4a4a4a 80%,#1e1e1e 100%)}
.hero-title{left:700px;top:280px;font-size:34px;font-weight:600;color:#fff}
.hero-sub{left:700px;top:322px;font-size:28px;font-weight:400;color:#fff}
.hero-script{left:700px;top:362px;font-size:32px;font-style:italic;color:#fff}
.hero-btn{left:700px;top:426px;width:192px;height:35px;background:var(--blue);color:#fff;font-size:12px;font-weight:700;text-align:center;line-height:35px}
.hero-arrow{top:483px;width:26px;height:28px;background:rgba(255,255,255,.25)}
.hero-arrow svg{display:block;margin:9px auto}

/* feature slider */
.feature{left:162px;top:552px;width:588px;height:269px;background:linear-gradient(120deg,#6b5a48 0%,#4b6c8d 45%,#24466f 100%)}
.feature-title{left:461px;top:630px;font-size:19px;font-weight:700;color:#fff;line-height:27px}
.feature-title .big{font-size:27px}
.feature-text{left:461px;top:694px;width:270px;font-size:13px;line-height:22px;color:#e9edf3}

/* section heads */
.section-head{left:162px;width:588px;height:26px;border-bottom:1px solid var(--rule)}
.section-head span{font-size:13px;font-weight:700;color:var(--blue)}
.widget-head{left:780px;width:258px;height:26px;border-bottom:1px solid var(--rule)}
.widget-head span{font-size:13px;font-weight:700;color:var(--blue)}

.photo{position:absolute}
.post-title{position:absolute;font-size:11.5px;font-weight:700;color:var(--ink);line-height:22px;text-transform:uppercase}
.post-date{position:absolute;font-size:11px;font-style:italic;color:var(--muted)}
.post-meta{position:absolute;font-size:11px;font-style:italic;color:var(--muted)}
.post-excerpt{position:absolute;font-size:12.5px;line-height:23px;color:var(--text)}

/* sidebar lists */
.recent{left:780px;top:598px;width:258px;list-style:none}
.recent li{height:29px;font-size:12px;color:#444;line-height:29px;padding-left:14px;position:relative;border-bottom:1px solid #f1f1f1}
.recent li::before{content:"›";position:absolute;left:2px;color:#999}
.cats{left:780px;top:980px;width:258px;list-style:none}
.cats>li{font-size:12.5px;color:#444;padding:13px 0 13px 16px;border-bottom:1px solid var(--rule);position:relative}
.cats>li::before{content:"›";position:absolute;left:4px;color:#999}
.cats ul{list-style:none;margin-top:8px}
.cats ul li{font-size:12px;padding:6px 0 6px 16px;position:relative}
.cats ul li::before{content:"›";position:absolute;left:2px;color:#999}

/* pagination */
.pager{left:365px;top:3743px;height:30px;display:flex;gap:6px}
.pager span{display:block;min-width:26px;height:30px;border:1px solid #d6d6d6;font-size:11px;color:#555;text-align:center;line-height:28px;padding:0 6px}

/* footer */
.footer{left:0;top:3825px;width:1200px;height:233px;background:var(--footer)}
.footer-col{position:absolute;top:55px;width:260px}
.footer-col h4{font-size:13px;font-weight:700;color:#fff;margin-bottom:12px}
.footer-col p{font-size:12px;line-height:23px;color:var(--footer-text)}
.footer-bottom{left:0;top:4058px;width:1200px;height:61px;background:var(--footer-bottom);font-size:11px;color:#9a9a9a}
.footer-bottom .copy{position:absolute;left:162px;top:22px}
.footer-bottom .flink{position:absolute;top:22px}
.footer-bottom .sep{position:absolute;top:22px;color:#555}
</style>
</head>
<body>
<div class="page">

  <!-- top bar -->
  <div class="abs topbar">
    <a class="link" style="left:197px">Home</a>
    <a class="link" style="left:289px">About Us</a>
    <a class="link" style="left:398px">Contact Us</a>
    <a class="link" style="left:516px">Resource</a>
    <span class="connect">Connect with our social network :</span>
    <span class="social" style="left:924px"></span>
    <span class="social" style="left:958px"></span>
    <span class="social" style="left:992px"></span>
    <span class="social" style="left:1024px"></span>
  </div>

  <!-- header -->
  <div class="abs brand">Nova Magazine</div>
  <div class="abs slogan">Site slogan goes here</div>
  <div class="abs ad" role="img" aria-label="Advertising banner for Blogcraft video tutorials"></div>

  <nav class="abs mainnav">
    <a class="item" style="left:40px">HOME</a>
    <a class="item" style="left:150px">ABOUT US</a>
    <a class="item" style="left:283px">CONTACT US</a>
    <a class="item" style="left:430px">RESOURCE</a>
    <div class="search">SEARCH
      <svg width="13" height="13" viewBox="0 0 13 13"><circle cx="5.5" cy="5.5" r="4" fill="none" stroke="#c8d3e6" stroke-width="1.6"/><line x1="8.5" y1="8.5" x2="12" y2="12" stroke="#c8d3e6" stroke-width="1.6"/></svg>
    </div>
  </nav>

  <!-- hero slider -->
  <div class="abs hero" role="img" aria-label="Black and white photo of an elegantly dressed couple"></div>
  <div class="abs hero-title">NOVA MAGAZINE</div>
  <div class="abs hero-sub">NOW HIGHLIGHT REVIEW</div>
  <div class="abs hero-script">Lorem ipsum</div>
  <a class="abs hero-btn">VIEW ALL MAGAZINES</a>
  <span class="abs hero-arrow" style="left:966px"><svg width="8" height="10" viewBox="0 0 8 10"><path d="M6 1 2 5l4 4" fill="none" stroke="#fff" stroke-width="1.6"/></svg></span>
  <span class="abs hero-arrow" style="left:995px"><svg width="8" height="10" viewBox="0 0 8 10"><path d="M2 1l4 4-4 4" fill="none" stroke="#fff" stroke-width="1.6"/></svg></span>

  <!-- feature slider -->
  <div class="abs feature" role="img" aria-label="Photo of a climber on a rock face against the sky"></div>
  <div class="abs feature-title">LOREM IPSUM IS<br><span class="big">SIMPLY DUMMY</span></div>
  <div class="abs feature-text">Lorem Ipsum is simply dummy text of the printing and typesetting...</div>

  <!-- latest news 1 -->
  <div class="abs section-head" style="top:845px"><span>LATEST NEWS</span></div>
  <div class="photo" style="left:162px;top:903px;width:182px;height:121px;background:linear-gradient(#eee,#777)" role="img" aria-label="Silhouette of a father and child by the sea"></div>
  <div class="photo" style="left:368px;top:903px;width:182px;height:121px;background:linear-gradient(90deg,#222,#bbb)" role="img" aria-label="Black and white portrait"></div>
  <div class="photo" style="left:568px;top:903px;width:182px;height:121px;background:linear-gradient(90deg,#c8102e,#eee 40%,#555)" role="img" aria-label="Vintage magazine cover"></div>
  <div class="post-title" style="left:162px;top:1035px;width:182px">Lorem ipsum is simply dummy text of the printing</div>
  <div class="post-title" style="left:368px;top:1035px;width:182px">Lorem ipsum is simply dummy text of the printing</div>
  <div class="post-title" style="left:568px;top:1035px;width:182px">Lorem ipsum is simply dummy text of the printing</div>
  <div class="post-date" style="left:162px;top:1083px">Posted on 27 March 2015</div>
  <div class="post-date" style="left:368px;top:1083px">Posted on 27 March 2015</div>
  <div class="post-date" style="left:568px;top:1083px">Posted on 27 March 2015</div>

  <!-- latest news 2 -->
  <div class="abs section-head" style="top:1136px"><span>LATEST NEWS</span></div>
  <div class="photo" style="left:162px;top:1195px;width:275px;height:173px;background:linear-gradient(135deg,#f4f4f4,#bdbdbd 60%,#c23 100%)" role="img" aria-label="Product photo of a white cube"></div>
  <div class="photo" style="left:475px;top:1195px;width:275px;height:173px;background:linear-gradient(90deg,#6a6a6a,#2b2b2b 50%,#9b7a5c)" role="img" aria-label="Portrait with magazine covers behind"></div>
  <div class="post-title" style="left:162px;top:1381px;width:275px">Lorem ipsum is simply dummy text of the printing</div>
  <div class="post-title" style="left:475px;top:1381px;width:275px">Lorem ipsum is simply dummy text of the printing</div>
  <div class="post-date" style="left:162px;top:1429px">Posted on 27 March 2015</div>
  <div class="post-date" style="left:475px;top:1429px">Posted on 27 March 2015</div>

  <!-- latest news 3 -->
  <div class="abs section-head" style="top:1479px"><span>LATEST NEWS</span></div>
  <div class="photo" style="left:162px;top:1538px;width:275px;height:186px;background:linear-gradient(135deg,#f2d21a,#1c1c1c 55%,#333)" role="img" aria-label="Music magazine cover with a portrait"></div>
  <div class="post-title" style="left:162px;top:1741px;width:275px">Lorem ipsum is simply dummy text of the printing</div>
  <div class="post-date" style="left:162px;top:1792px">Posted on 27 March 2015</div>
  <div class="photo" style="left:478px;top:1538px;width:96px;height:77px;background:linear-gradient(#a7c46a,#5a7a2e)" role="img" aria-label="Person lying in grass"></div>
  <div class="photo" style="left:478px;top:1631px;width:96px;height:77px;background:linear-gradient(#c9a590,#6a4a3a)" role="img" aria-label="Portrait"></div>
  <div class="photo" style="left:478px;top:1725px;width:96px;height:79px;background:linear-gradient(#e2c83c,#c53a4a)" role="img" aria-label="Colourful magazine cover"></div>
  <div class="post-title" style="left:590px;top:1535px;width:160px">Lorem ipsum is simply dummy text</div>
  <div class="post-date" style="left:590px;top:1584px">Posted on 27 March 2015</div>
  <div class="post-title" style="left:590px;top:1628px;width:160px">Lorem ipsum is simply dummy text</div>
  <div class="post-date" style="left:590px;top:1677px">Posted on 27 March 2015</div>
  <div class="post-title" style="left:590px;top:1722px;width:160px">Lorem ipsum is simply dummy text</div>
  <div class="post-date" style="left:590px;top:1771px">Posted on 27 March 2015</div>

  <!-- latest news 4 -->
  <div class="abs section-head" style="top:1839px"><span>LATEST NEWS</span></div>
  <div class="photo" style="left:162px;top:1895px;width:93px;height:79px;background:linear-gradient(#e6e6e6,#7a5e4a)" role="img" aria-label="Portrait with sunglasses"></div>
  <div class="photo" style="left:162px;top:1988px;width:93px;height:80px;background:linear-gradient(#2a2a2a,#6b6b6b)" role="img" aria-label="Black and white portrait"></div>
  <div class="photo" style="left:162px;top:2081px;width:93px;height:80px;background:linear-gradient(#d94a4a,#f0dede)" role="img" aria-label="Magazine cover portrait"></div>
  <div class="photo" style="left:478px;top:1895px;width:93px;height:79px;background:linear-gradient(#9c1c24,#e8d6cc)" role="img" aria-label="Fashion magazine cover"></div>
  <div class="photo" style="left:478px;top:1988px;width:93px;height:80px;background:linear-gradient(#d9c3b4,#3a2a22)" role="img" aria-label="Portrait"></div>
  <div class="photo" style="left:478px;top:2081px;width:93px;height:80px;background:linear-gradient(#f0f0f0,#444)" role="img" aria-label="Black and white magazine cover"></div>
  <div class="post-title" style="left:272px;top:1892px;width:160px">Lorem ipsum is simply dummy text</div>
  <div class="post-date" style="left:272px;top:1941px">Posted on 27 March 2015</div>
  <div class="post-title" style="left:272px;top:1985px;width:160px">Lorem ipsum is simply dummy text</div>
  <div class="post-date" style="left:272px;top:2034px">Posted on 27 March 2015</div>
  <div class="post-title" style="left:272px;top:2078px;width:160px">Lorem ipsum is simply dummy text</div>
  <div class="post-date" style="left:272px;top:2127px">Posted on 27 March 2015</div>
  <div class="post-title" style="left:590px;top:1892px;width:160px">Lorem ipsum is simply dummy text</div>
  <div class="post-date" style="left:590px;top:1941px">Posted on 27 March 2015</div>
  <div class="post-title" style="left:590px;top:1985px;width:160px">Lorem ipsum is simply dummy text</div>
  <div class="post-date" style="left:590px;top:2034px">Posted on 27 March 2015</div>
  <div class="post-title" style="left:590px;top:2078px;width:160px">Lorem ipsum is simply dummy text</div>
  <div class="post-date" style="left:590px;top:2127px">Posted on 27 March 2015</div>

  <!-- latest news 5 -->
  <div class="abs section-head" style="top:2207px"><span>LATEST NEWS</span></div>
  <div class="photo" style="left:162px;top:2268px;width:233px;height:170px;background:linear-gradient(#b9cbe0,#7c8a6e 55%,#5a4a3a)" role="img" aria-label="Two hikers in the mountains"></div>
  <div class="post-title" style="left:426px;top:2270px;width:320px">Lorem ipsum is simply dummy text of the printing and typesetting industry.</div>
  <div class="post-meta" style="left:426px;top:2322px">Category : Lorem Ipsum &nbsp;&nbsp; / &nbsp;&nbsp; Posted on 27 March 2015</div>
  <div class="post-excerpt" style="left:426px;top:2350px;width:322px">Lorem Ipsum is simply dummy text of the printing and type-setting industry. Lorem Ipsum has been the industry's standard dummy text ever since the 1500s, when an unknown printer took a galley of type and scrambled...</div>
  <div class="photo" style="left:162px;top:2477px;width:233px;height:170px;background:linear-gradient(#9fd0ef,#c9e3f3 50%,#7ab050)" role="img" aria-label="Children jumping on a beach"></div>
  <div class="post-title" style="left:426px;top:2479px;width:320px">Lorem ipsum is simply dummy text of the printing and typesetting industry.</div>
  <div class="post-meta" style="left:426px;top:2531px">Category : Lorem Ipsum &nbsp;&nbsp; / &nbsp;&nbsp; Posted on 27 March 2015</div>
  <div class="post-excerpt" style="left:426px;top:2559px;width:322px">Lorem Ipsum is simply dummy text of the printing and type-setting industry. Lorem Ipsum has been the industry's standard dummy text ever since the 1500s, when an unknown printer took a galley of type and scrambled...</div>

  <!-- latest news 6 -->
  <div class="abs section-head" style="top:2690px"><span>LATEST NEWS</span></div>
  <div class="photo" style="left:162px;top:2751px;width:588px;height:242px;background:linear-gradient(90deg,#1a1a1a,#6e6e6e 40%,#2a2a2a 75%,#111)" role="img" aria-label="Black and white photo of an athlete in a gym"></div>
  <div class="post-title" style="left:162px;top:3018px;width:588px">Lorem ipsum is simply dummy text of the printing and typesetting industry.</div>
  <div class="post-meta" style="left:162px;top:3049px">Category : Lorem Ipsum &nbsp;&nbsp; / &nbsp;&nbsp; Posted on 27 March 2015</div>
  <div class="abs" style="left:162px;top:3076px;width:588px;border-top:1px solid var(--rule)"></div>
  <div class="post-excerpt" style="left:162px;top:3094px;width:588px">Lorem Ipsum is simply dummy text of the printing and typesetting industry. Lorem Ipsum has been the industry's standard dummy text ever since the 1500s, when an unknown printer took a galley of type and scrambled it to make a type specimen book. It has survived not only five centuries, but also the leap into electronic typesetting, remaining essentially unchanged. It was popularised in the 1960s with the release of Letraset sheets containing Lorem Ipsum passages, and more recently with desktop...</div>
  <div class="photo" style="left:162px;top:3251px;width:588px;height:239px;background:linear-gradient(#f6c25a,#e98a2a 50%,#7a3e18)" role="img" aria-label="Elderly couple walking at sunset"></div>
  <div class="post-title" style="left:162px;top:3512px;width:588px">Lorem ipsum is simply dummy text of the printing and typesetting industry.</div>
  <div class="post-meta" style="left:162px;top:3546px">Category : Lorem Ipsum &nbsp;&nbsp; / &nbsp;&nbsp; Posted on 27 March 2015</div>
  <div class="abs" style="left:162px;top:3573px;width:588px;border-top:1px solid var(--rule)"></div>
  <div class="post-excerpt" style="left:162px;top:3591px;width:588px">Lorem Ipsum is simply dummy text of the printing and typesetting industry. Lorem Ipsum has been the industry's standard dummy text ever since the 1500s, when an unknown printer took a galley of type and scrambled it to make a type specimen book. It has survived not only five centuries, but also the leap into electronic typesetting, remaining essentially unchanged. It was popularised in the 1960s with the release of Letraset sheets containing Lorem Ipsum passages, and more recently with desktop...</div>

  <div class="abs pager">
    <span>Prev</span><span>1</span><span>2</span><span>3</span><span>4</span><span>5</span><span>6</span><span>...</span><span>22</span><span>Next</span>
  </div>

  <!-- sidebar -->
  <div class="abs widget-head" style="top:550px"><span>RECENT POSTS</span></div>
  <ul class="abs recent">
    <li>Lorem Ipsum is simply dummy text</li>
    <li>Lorem Ipsum is dummy simply dummy text</li>
    <li>Lorem Ipsum is simply dummy text</li>
    <li>Lorem Ipsum is simply dummy text</li>
    <li>Lorem Ipsum sdummy simply</li>
    <li>Lorem Ipsum simply</li>
    <li>Lorem Ipsum is simply dummy text</li>
    <li>Lorem Ipsum</li>
    <li>Lorem Ipsum is simply dummy text</li>
    <li>Lorem Ipsum is simply</li>
    <li>Lorem Ipsum is simply dummy</li>
  </ul>

  <div class="abs widget-head" style="top:940px"><span>CATEGORY</span></div>
  <ul class="abs cats">
    <li>Lorem Ipsum is simply</li>
    <li>Lorem Ipsum is simply dummy text</li>
    <li>Lorem Ipsum is simply dummy
      <ul>
        <li>Lorem Ipsum is simply dummy</li>
        <li>Lorem Ipsum is simply</li>
        <li>Lorem Ipsum</li>
        <li>Lorem Ipsum is simply</li>
        <li>Lorem Ipsum simply</li>
      </ul>
    </li>
    <li>Lorem Ipsum is simply</li>
    <li>Lorem Ipsum</li>
    <li>Lorem Ipsum is simply lorem ipsum</li>
    <li>Lorem Ipsum is simply</li>
    <li>Lorem Ipsum is simply simply</li>
  </ul>

  <div class="abs widget-head" style="top:1536px"><span>MOST POPULAR POSTS</span></div>
  <div class="photo" style="left:780px;top:1587px;width:96px;height:80px;background:linear-gradient(#d8d8d8,#4a3a30)" role="img" aria-label="Portrait with hat"></div>
  <div class="photo" style="left:780px;top:1688px;width:96px;height:78px;background:linear-gradient(#cbb6a6,#3a3a3a)" role="img" aria-label="Portrait"></div>
  <div class="photo" style="left:780px;top:1785px;width:96px;height:77px;background:linear-gradient(#f0f0f0,#222)" role="img" aria-label="Black and white magazine cover"></div>
  <div class="photo" style="left:780px;top:1884px;width:96px;height:77px;background:linear-gradient(#e3c83a,#c33a4a)" role="img" aria-label="Colourful magazine cover"></div>
  <div class="post-title" style="left:895px;top:1585px;width:143px">Lorem ipsum is simply dummy text</div>
  <div class="post-date" style="left:895px;top:1634px">Posted on 27 March 2015</div>
  <div class="post-title" style="left:895px;top:1685px;width:143px">Lorem ipsum is simply dummy text</div>
  <div class="post-date" style="left:895px;top:1734px">Posted on 27 March 2015</div>
  <div class="post-title" style="left:895px;top:1782px;width:143px">Lorem ipsum is simply dummy text</div>
  <div class="post-date" style="left:895px;top:1831px">Posted on 27 March 2015</div>
  <div class="post-title" style="left:895px;top:1881px;width:143px">Lorem ipsum is simply dummy text</div>
  <div class="post-date" style="left:895px;top:1930px">Posted on 27 March 2015</div>

  <!-- footer -->
  <footer class="abs footer">
    <div class="footer-col" style="left:162px"><h4>LOREM IPSUM IS SIMPLY</h4><p>Lorem Ipsum is simply dummy text of the printing and typesetting industry. Lorem Ipsum has been the industry's standard dummy text ever since the 1500s, when an unknown printer took a galley of type and scrambled...</p></div>
    <div class="footer-col" style="left:470px"><h4>LOREM IPSUM IS SIMPLY</h4><p>Lorem Ipsum is simply dummy text of the printing and typesetting industry. Lorem Ipsum has been the industry's standard dummy text ever since the 1500s, when an unknown printer took a galley of type and scrambled...</p></div>
    <div class="footer-col" style="left:777px"><h4>LOREM IPSUM IS SIMPLY</h4><p>Lorem Ipsum is simply dummy text of the printing and typesetting industry. Lorem Ipsum has been the industry's standard dummy text ever since the 1500s, when an unknown printer took a galley of type and scrambled...</p></div>
  </footer>
  <div class="abs footer-bottom">
    <span class="copy">© 2015, Nova Magazine, All rights reserved, Privacy Policy</span>
    <a class="flink" style="left:720px">Home</a>
    <span class="sep" style="left:778px">/</span>
    <a class="flink" style="left:806px">About Us</a>
    <span class="sep" style="left:882px">/</span>
    <a class="flink" style="left:910px">Contact Us</a>
    <span class="sep" style="left:985px">/</span>
    <a class="flink" style="left:1000px">Resource</a>
  </div>

</div>
</body>
</html>
```